Kestrel Facilities Business Card Design

We would now like to design business cards with the new Kestrel Facilities logo

Target Market(s)

Professional

Industry/Entity Type

Professional services

Contact Information for Business Card

Employee name, title, phone number, email address, corporate office address and logo.

Font styles to use
Sans Serif

Colors
0054AA
0677BA
7BADD7
CADEEF
E8F1F8

Requirements
Must have
• My logo
Should not have
• any other pictures or images besides my logo

```html
<!DOCTYPE html>
<html lang="en">
<head>
<meta charset="utf-8">
<title>Kestrel Facilities Business Card</title>
<link href="https://fonts.googleapis.com/css2?family=Oswald:wght@500&family=Roboto:wght@400&display=swap" rel="stylesheet">
<style>
  :root {
    --backdrop: #4d4d4d;
    --paper: #ececec;
    --brand-blue: #0a7fe8;
    --brand-blue-light: #1a90f2;
    --brand-blue-deep: #0675e0;
    --ink: #505050;
    --white: #ffffff;
  }
  * { margin: 0; padding: 0; box-sizing: border-box; }
  html, body { width: 1200px; height: 963px; overflow: hidden; }
  body { background: var(--backdrop); position: relative; font-family: "Roboto", sans-serif; }

  .card { position: absolute; top: 174px; width: 316px; height: 556px; }

  /* Front */
  .card-front { left: 222px; background: var(--paper); }
  .card-frame {
    position: absolute; left: 18px; top: 16px; right: 16px; bottom: 15px;
    border: 3px solid var(--brand-blue);
  }
  .person { position: absolute; top: 158px; width: 100%; text-align: center; }
  .person-name {
    font-family: "Oswald", sans-serif; font-weight: 500; color: var(--brand-blue);
    font-size: 26px; line-height: 30px; letter-spacing: 0.2px; text-transform: uppercase;
  }
  .person-title {
    font-family: "Oswald", sans-serif; font-weight: 500; color: var(--ink);
    font-size: 16px; line-height: 18px; font-variant: small-caps; letter-spacing: 0.3px;
  }
  .divider { position: absolute; left: 65px; width: 188px; height: 1px; background: var(--brand-blue); }
  .icon-row {
    position: absolute; left: 0; width: 100%; display: flex; justify-content: center; gap: 5px;
  }
  .icon-box {
    width: 19px; height: 19px; background: var(--brand-blue);
    display: flex; align-items: center; justify-content: center;
  }
  .icon-box svg { width: 12px; height: 12px; }
  .info {
    position: absolute; width: 100%; text-align: center;
    font-size: 14px; line-height: 17.5px; color: var(--ink);
  }

  /* Back */
  .card-back {
    left: 637px;
    background: linear-gradient(180deg, var(--brand-blue-light) 0%, var(--brand-blue) 50%, var(--brand-blue-deep) 100%);
    overflow: hidden;
  }
  .back-texture {
    position: absolute; inset: 0;
    background: linear-gradient(160deg, rgba(255,255,255,0.06), rgba(0,0,0,0.04));
  }
  .brand-lockup {
    position: absolute; left: 0; right: 0; top: 244px;
    display: flex; align-items: center; justify-content: center; gap: 12px;
  }
  .brand-square { width: 22px; height: 22px; background: var(--white); }
  .brand-name {
    font-family: "Oswald", sans-serif; font-weight: 500; color: var(--white);
    font-size: 40px; line-height: 44px; text-transform: uppercase; letter-spacing: 1px;
  }
</style>
</head>
<body>

<section class="card card-front" aria-label="Business card front">
  <div class="card-frame"></div>

  <div class="person">
    <h1 class="person-name">Daniel Reyes</h1>
    <p class="person-title">President</p>
  </div>

  <div class="divider" style="top:226px"></div>
  <div class="icon-row" style="top:216px">
    <span class="icon-box" aria-label="Address">
      <svg viewBox="0 0 12 12"><path d="M6 1a3.3 3.3 0 0 0-3.3 3.3C2.7 6.8 6 11 6 11s3.3-4.2 3.3-6.7A3.3 3.3 0 0 0 6 1z" fill="#fff"/><circle cx="6" cy="4.3" r="1.2" fill="#0a7fe8"/></svg>
    </span>
  </div>
  <p class="info" style="top:240px">4120 Birchwood Court<br>Fairbanks, Alaska 34588</p>

  <div class="divider" style="top:294px"></div>
  <div class="icon-row" style="top:284px">
    <span class="icon-box" aria-label="Office phone">
      <svg viewBox="0 0 12 12"><path d="M3 1.2l1.6 2.2-.9 1.1c.7 1.5 1.8 2.6 3.3 3.3l1.1-.9 2.2 1.6-.7 1.9C5.3 10.2 1.8 6.7 1.1 2l1.9-.8z" fill="#fff"/></svg>
    </span>
    <span class="icon-box" aria-label="Mobile phone">
      <svg viewBox="0 0 12 12"><rect x="3" y="0.8" width="6" height="10.4" rx="0.8" fill="none" stroke="#fff" stroke-width="1.3"/><rect x="5" y="9" width="2" height="1" fill="#fff"/></svg>
    </span>
    <span class="icon-box" aria-label="Email">
      <svg viewBox="0 0 12 12"><rect x="1.2" y="2.8" width="9.6" height="6.6" fill="#fff"/><path d="M1.2 2.8L6 6.6l4.8-3.8" fill="none" stroke="#0a7fe8" stroke-width="1"/></svg>
    </span>
  </div>
  <p class="info" style="top:312px">555-310-4478<br>555-642-1193<br>info@kestrelfacilities.com</p>

  <div class="divider" style="top:373px"></div>
  <p class="info" style="top:382px">KestrelFacilities.com</p>
</section>

<section class="card card-back" aria-label="Business card back">
  <div class="back-texture" role="img" aria-label="Soft blue background texture"></div>
  <div class="brand-lockup">
    <span class="brand-square"></span>
    <p class="brand-name">Kestrel<br>Facilities</p>
  </div>
</section>

</body>
</html>
```